Create a wordpress website for Tovarin business solution

This project is to create a complete website with all pages.

Overview
The purpose of this project is to create a full complete website with all pages (16 pages). The site should be professional and modern. The site is for an IT recruiting and IT training company. The site needs to be easy to administer and update content. It should be simple to add pages, videos and testimonials later. I will leave the site layout, color schemes and flow to the designers.

Navigation Menu (Home, who we are, what we do, what makes us different, why it matters, candidate portal, contact us, Blog)

WHO WE ARE should be a drop down menu with link to pages (about us, mission, vision and purpose, our team)

WHAT WE DO should be drop down menu with link to the following pages (IT Recruiting, IT Training, Hardware and software sales)

What makes us different should be single page with different paragraph titles. (We live what we do, we don't compromise quality, we share knowledge, staffing guarantee)

Why it matters should be single page with paragraph titles. (Quickly fill positions, candidate career development)

Candidate portal should links to my portal login page. I can add the correct URL later. I just need it to link to somewhere. I can change it.

Contact us should have (address, phone number, google map and a form to submit request for a call back)

Blog - This link should launch a wordpress blogging module

Target Market(s)

IT RECRUITING AND CONSULTING

Industry/Entity Type

It Company

Coding

Coded - Design and coding required

Requirements
Must have
• Company Logo
• Navigation Menu (Home, who we are, what we do, what makes us different, why it matters, candidate portal, contact us)
• WHO WE ARE should be a drop down menu with link to pages (about us, mission, vision and purpose, our team)
• WHAT WE DO should be drop down menu with link to the following pages (IT Recruiting, IT Training, Hardware and software sales)
• What makes us different should be single page with different paragraph titles. (We live what we do, we don't compromise quality, we share knowledge, staffing guarantee)
• Why it matters should be single page with paragraph titles. (Quickly fill positions, candidate career development)
• Candidate portal should links to my portal login page. I can add the correct URL later. I just need it to link to somewhere. I can change it.
• Contact us should have (address, phone number, google map and a form to submit request for a call back)

```html
<!DOCTYPE html>
<html lang="en">
<head>
<meta charset="utf-8">
<title>Tovarin Business Solution</title>
<link href="https://fonts.googleapis.com/css2?family=Montserrat:wght@300;400;500;600&family=Open+Sans:wght@400;600&display=swap" rel="stylesheet">
<style>
:root{
  --blue:#0a55a0;
  --blue-dark:#0b3f78;
  --orange:#e8771a;
  --orange-light:#fba94b;
  --brown:#9a5406;
  --ink:#222;
  --text:#666;
  --white:#fff;
}
*{margin:0;padding:0;box-sizing:border-box}
html,body{width:1200px;height:2406px;overflow:hidden;background:var(--white)}
body{position:relative;font-family:"Open Sans",Arial,sans-serif;color:var(--text)}
.abs{position:absolute}
.heading{font-family:"Montserrat",Arial,sans-serif;font-weight:300;color:var(--ink);letter-spacing:1px}

/* hero */
.hero{left:0;top:0;width:1200px;height:614px;background:linear-gradient(100deg,#f4f8fb 0%,#e6eef3 40%,#c9cfd2 65%,#8e8a86 85%,#d6dde0 100%)}
.brand{left:77px;top:8px;font-family:"Montserrat",sans-serif;font-weight:500;font-size:92px;color:var(--blue);letter-spacing:-1px;line-height:1}
.brand-sub{left:120px;top:104px;font-family:"Montserrat",sans-serif;font-size:21px;color:#555;letter-spacing:3px}
.call-icon{left:861px;top:25px;width:52px;height:52px;border-radius:50%;background:var(--orange)}
.call-label{left:930px;top:28px;font-family:"Montserrat",sans-serif;font-size:15px;color:var(--ink)}
.call-number{left:930px;top:46px;font-family:"Montserrat",sans-serif;font-weight:500;font-size:28px;color:var(--blue)}
.hero-title{left:80px;top:276px;font-size:43px;line-height:62px;color:#1d1d1d}
.btn{display:flex;align-items:center;justify-content:center;border-radius:40px;font-family:"Montserrat",sans-serif;color:var(--white)}
.hero-cta{left:77px;top:417px;width:210px;height:61px;background:var(--orange);font-size:21px}

/* navigation */
.nav{left:0;top:614px;width:1200px;height:63px;background:var(--blue)}
.nav-item{top:0;height:63px;display:flex;align-items:center;font-family:"Montserrat",sans-serif;font-size:13.5px;color:var(--white)}
.nav-item.active{background:var(--orange);justify-content:center}

/* welcome */
.welcome-title{left:0;width:1200px;top:716px;text-align:center;font-size:38px}
.welcome-title span{color:var(--blue);font-weight:400}
.welcome-text{left:140px;width:920px;top:788px;text-align:center;font-size:14px;line-height:23px}
.welcome-text b{color:#333}
.read-more{left:528px;top:908px;width:144px;height:50px;background:var(--blue);font-size:14px;font-weight:600}

/* services */
.service{top:1010px;width:348px;height:395px;color:var(--white);text-align:center}
.service svg.icon{display:block;margin:62px auto 0}
.service h3{font-family:"Montserrat",sans-serif;font-weight:400;font-size:21px;margin-top:22px}
.service p{font-size:13.5px;line-height:23px;margin:18px auto 0;width:290px}
.service .more{display:block;margin:26px auto 0}
.s1{left:77px;background:var(--orange-light)}
.s1 h3{color:var(--blue)}
.s1 p{color:#8a5418}
.s2{left:426px;background:var(--orange)}
.s3{left:775px;background:var(--brown)}

/* testimonials & blog */
.section-title{font-size:40px}
.quote{left:80px;top:1522px;width:560px;font-size:13.5px;line-height:24px}
.quote .mark{font-family:Georgia,serif;font-size:40px;color:#aaa;line-height:0;vertical-align:-10px}
.avatar{left:93px;top:1639px;width:112px;height:112px;border-radius:50%;border:4px solid #e3e3e3;background:radial-gradient(circle at 50% 40%,#f1d9b8,#c89a6b 60%,#a8c6d9)}
.person{left:252px;top:1678px;font-family:"Montserrat",sans-serif;font-size:20px;color:var(--blue)}
.place{left:252px;top:1704px;font-size:13px;font-style:italic;color:#888;letter-spacing:1px}
.post-img{width:112px;height:112px;border:3px solid #eee}
.post-title{font-family:"Montserrat",sans-serif;font-size:17px;color:#333}
.post-date{font-size:12px;color:#999}
.post-text{width:290px;font-size:13.5px;line-height:23px}

/* contact */
.contact{left:0;top:1822px;width:1200px;height:584px;background:linear-gradient(110deg,#1f5d9a 0%,#2f6aa3 45%,#1c5590 75%,#2a6aa5 100%)}
.contact-title{left:0;width:1200px;top:1862px;text-align:center;color:var(--white);font-size:38px}
.field{left:77px;width:436px;background:var(--white);border-radius:4px;font-size:14px;color:#999;padding:14px 16px}
.submit{left:77px;top:2239px;width:167px;height:52px;background:var(--orange);font-size:20px;font-weight:500}
.map{left:534px;top:1947px;width:276px;height:276px;border:3px solid #e8e8e8;background:linear-gradient(135deg,#a8aeb2,#c4c8cb 50%,#9ea4a8)}
.addr-title{left:855px;top:1946px;font-family:"Montserrat",sans-serif;font-weight:600;font-size:19px;color:var(--white);letter-spacing:1px}
.addr-line{left:855px;color:var(--white);font-size:14px;line-height:22px}
.addr-text{left:887px;color:var(--white);font-size:14px;line-height:22px}
.addr-text .name{font-family:"Montserrat",sans-serif;font-size:17px}
.social{top:2239px;width:38px;height:38px;border-radius:3px}
.footer-rule{left:77px;top:2345px;width:1046px;height:1px;background:rgba(255,255,255,.3)}
.copyright{left:0;width:1200px;top:2364px;text-align:center;color:var(--white);font-size:13px}
.copyright span{color:var(--orange-light)}
</style>
</head>
<body>

<div class="abs hero" role="img" aria-label="Photo of a young man working on a laptop in a bright café"></div>
<div class="abs brand">Tovarin</div>
<div class="abs brand-sub">BUSINESS SOLUTION LLC</div>
<div class="abs call-icon">
  <svg width="52" height="52" viewBox="0 0 52 52"><path d="M19 15c2 0 3 4 4 6s-2 3-2 4c1 3 4 6 7 7 1 0 2-3 4-2s6 2 6 4-3 5-6 5c-9-1-17-9-18-18 0-3 3-6 5-6z" fill="#fff"/></svg>
</div>
<div class="abs call-label">Call Us On</div>
<div class="abs call-number">(555) 204-7316</div>

<h1 class="abs heading hero-title">TRANSFORMING THE<br>LEARNING EXPERIENCE</h1>
<a class="abs btn hero-cta">CONTACT US</a>

<nav class="abs nav">
  <div class="abs nav-item active" style="left:71px;width:83px">HOME</div>
  <div class="abs nav-item" style="left:172px">WHO WE ARE</div>
  <div class="abs nav-item" style="left:305px">WHAT WE DO</div>
  <div class="abs nav-item" style="left:440px">WHAT MAKE US DIFFERENT</div>
  <div class="abs nav-item" style="left:672px">WHY IT MATTERS</div>
  <div class="abs nav-item" style="left:833px">CANDIDATE PORTAL</div>
  <div class="abs nav-item" style="left:1017px">CONTACT US</div>
</nav>

<h2 class="abs heading welcome-title">WELCOME TO <span>Tovarin</span></h2>
<p class="abs welcome-text"><b>Lorem Ipsum is simply dummy text of the printing and typesetting industry.</b>Lorem Ipsum has been the industry's standard dummy text ever since the 1500s, when an unknown printer took a galley of type and scrambled it to make a type specimen book. It has survived not only five centuries, but also the leap into electronic typesetting, remaining essentially unchanged. It was popularised in the 1960s with the release of Letraset sheets containing Lorem Ipsum passages, and more recently with desktop publishing.</p>
<a class="abs btn read-more">READ MORE</a>

<section class="abs service s1">
  <svg class="icon" width="96" height="96" viewBox="0 0 96 96" fill="#fff">
    <circle cx="26" cy="28" r="9"/><circle cx="70" cy="28" r="9"/>
    <path d="M10 58c0-10 7-16 16-16h4v16z"/><path d="M86 58c0-10-7-16-16-16h-4v16z"/>
    <circle cx="48" cy="46" r="17" fill="none" stroke="#fff" stroke-width="6"/>
    <circle cx="48" cy="43" r="6"/><path d="M38 56c2-5 6-7 10-7s8 2 10 7z"/>
    <path d="M60 58l18 18" stroke="#fff" stroke-width="8" stroke-linecap="round"/>
  </svg>
  <h3>IT Recruiting</h3>
  <p>Lorem Ipsum is simply dummy text of the printing and typesetting industry. Lorem Ipsum has been the industry's.</p>
  <svg class="more" width="46" height="46" viewBox="0 0 46 46"><circle cx="23" cy="23" r="21" fill="none" stroke="#0a55a0" stroke-width="2.5"/><path d="M17 16l7 7-7 7M23 16l7 7-7 7" fill="none" stroke="#0a55a0" stroke-width="2"/></svg>
</section>

<section class="abs service s2">
  <svg class="icon" width="96" height="96" viewBox="0 0 96 96" fill="#fff">
    <rect x="36" y="14" width="54" height="40" fill="none" stroke="#fff" stroke-width="5"/>
    <path d="M48 54l-8 26M78 54l8 26" stroke="#fff" stroke-width="4"/>
    <circle cx="20" cy="32" r="9"/>
    <path d="M8 80V52c0-6 4-10 10-10h6l20-10 3 5-20 14v29z"/>
  </svg>
  <h3>IT Training</h3>
  <p>Lorem Ipsum is simply dummy text of the printing and typesetting industry. Lorem Ipsum has been the industry's.</p>
  <svg class="more" width="46" height="46" viewBox="0 0 46 46"><circle cx="23" cy="23" r="21" fill="none" stroke="#fff" stroke-width="2.5"/><path d="M17 16l7 7-7 7M23 16l7 7-7 7" fill="none" stroke="#fff" stroke-width="2"/></svg>
</section>

<section class="abs service s3">
  <svg class="icon" width="96" height="96" viewBox="0 0 96 96">
    <rect x="4" y="12" width="88" height="58" rx="4" fill="none" stroke="#fff" stroke-width="5"/>
    <path d="M44 70v12h8V70M30 84h36" stroke="#fff" stroke-width="5" fill="none"/>
  </svg>
  <h3>Hardware &amp; Software Sales</h3>
  <p>Lorem Ipsum is simply dummy text of the printing and typesetting industry. Lorem Ipsum has been the industry's.</p>
  <svg class="more" width="46" height="46" viewBox="0 0 46 46"><circle cx="23" cy="23" r="21" fill="none" stroke="#fff" stroke-width="2.5"/><path d="M17 16l7 7-7 7M23 16l7 7-7 7" fill="none" stroke="#fff" stroke-width="2"/></svg>
</section>

<h2 class="abs heading section-title" style="left:80px;top:1444px">TESTIMONIALS</h2>
<p class="abs quote"><span class="mark">&ldquo;</span> Lorem Ipsum is simply dummy text of the printing and typesetting industry. Lorem Ipsum has been the industry's standard dummy text ever since the 1500s, when an unknown printer took a galley of type and scrambled it to make a type specimen book. It has survived not only five centuries. <span class="mark">&rdquo;</span></p>
<div class="abs avatar" role="img" aria-label="Portrait photo of the client giving the testimonial"></div>
<div class="abs person">CLARA WHITFIELD</div>
<div class="abs place">LONDON</div>

<h2 class="abs heading section-title" style="left:697px;top:1444px">BLOG POST</h2>

<div class="abs post-img" style="left:695px;top:1519px;background:linear-gradient(135deg,#5f8a9c,#c9d6dc 50%,#3f5e6c)" role="img" aria-label="Photo of a team meeting around a table, seen from above"></div>
<div class="abs post-title" style="left:823px;top:1519px">Lorem Ipsum is simply dummy</div>
<div class="abs post-date" style="left:823px;top:1545px"><svg width="13" height="13" viewBox="0 0 13 13" style="vertical-align:-2px;margin-right:6px"><rect x="1" y="2" width="11" height="10" fill="none" stroke="#0a55a0" stroke-width="1.5"/><path d="M1 5h11M4 0v3M9 0v3" stroke="#0a55a0" stroke-width="1.5"/></svg>20 March 2016</div>
<p class="abs post-text" style="left:823px;top:1568px">Lorem Ipsum is simply dummy text of the printing and typesetting industry. Lorem Ipsum has been the industry's standard</p>

<div class="abs post-img" style="left:695px;top:1654px;background:linear-gradient(135deg,#e9e3da,#b99a7a 55%,#6d5a4a)" role="img" aria-label="Photo of two colleagues working on a laptop"></div>
<div class="abs post-title" style="left:823px;top:1654px">Lorem Ipsum is simply dummy</div>
<div class="abs post-date" style="left:823px;top:1680px"><svg width="13" height="13" viewBox="0 0 13 13" style="vertical-align:-2px;margin-right:6px"><rect x="1" y="2" width="11" height="10" fill="none" stroke="#0a55a0" stroke-width="1.5"/><path d="M1 5h11M4 0v3M9 0v3" stroke="#0a55a0" stroke-width="1.5"/></svg>20 March 2016</div>
<p class="abs post-text" style="left:823px;top:1703px">Lorem Ipsum is simply dummy text of the printing and typesetting industry. Lorem Ipsum has been the industry's standard</p>

<section class="abs contact" role="img" aria-label="Blue-tinted photo of a person working at a café table"></section>
<h2 class="abs heading contact-title">CONTACT US</h2>

<div class="abs field" style="top:1947px;height:52px">Name</div>
<div class="abs field" style="top:2005px;height:52px">E-Mail</div>
<div class="abs field" style="top:2063px;height:52px">Subject</div>
<div class="abs field" style="top:2120px;height:103px">Message</div>
<a class="abs btn submit">SUBMIT</a>

<div class="abs map" role="img" aria-label="Street map with a location pin for the office"></div>

<div class="abs addr-title">CONTACT ADDRESS</div>
<svg class="abs" style="left:853px;top:1994px" width="22" height="28" viewBox="0 0 22 28"><path d="M11 2a8 8 0 0 0-8 8c0 6 8 15 8 15s8-9 8-15a8 8 0 0 0-8-8z" fill="none" stroke="#fff" stroke-width="1.8"/><circle cx="11" cy="10" r="3" fill="none" stroke="#fff" stroke-width="1.8"/></svg>
<div class="abs addr-text" style="top:1987px"><span class="name">Tovarin Business Solution</span><br>123 Building Name, Street Name,<br>Area, City Name,<br>Country - Zipcode</div>
<svg class="abs" style="left:853px;top:2102px" width="20" height="20" viewBox="0 0 20 20"><path d="M5 2c1 0 2 3 2 4s-2 1-1 3 3 4 5 5 1-1 3-1 4 1 4 2-2 3-4 3C8 18 2 12 2 5c0-2 2-3 3-3z" fill="none" stroke="#fff" stroke-width="1.5"/></svg>
<div class="abs addr-text" style="top:2100px">(555) 204-7316</div>
<svg class="abs" style="left:852px;top:2142px" width="22" height="20" viewBox="0 0 22 20"><rect x="5" y="1" width="12" height="6" fill="none" stroke="#fff" stroke-width="1.5"/><rect x="1" y="7" width="20" height="8" fill="none" stroke="#fff" stroke-width="1.5"/><rect x="5" y="12" width="12" height="7" fill="none" stroke="#fff" stroke-width="1.5"/></svg>
<div class="abs addr-text" style="top:2141px">(555) 204-7316</div>
<svg class="abs" style="left:853px;top:2186px" width="20" height="14" viewBox="0 0 20 14"><rect x="1" y="1" width="18" height="12" fill="none" stroke="#fff" stroke-width="1.5"/><path d="M1 1l9 7 9-7" fill="none" stroke="#fff" stroke-width="1.5"/></svg>
<div class="abs addr-text" style="top:2182px">info@tovarin.com</div>

<div class="abs social" style="left:855px;background:#3b5a9a"></div>
<div class="abs social" style="left:903px;background:#0a7ac2"></div>

<div class="abs footer-rule"></div>
<div class="abs copyright">&copy; <span>Tovarin Business Solution LLC</span> &ndash; 2016. All Rights Reserved.</div>

</body>
</html>
```